Logo for Brook Partners LLC needs a design

This logo will be for a food handler and restaurant manager training business located. I am a registered trainer and proctor for KitchTrue, the Allied Eatery Federation. colors options should be black, white, blue, silver or something else bold. The file that I have sent needs to be on the card somewhere, small.

need to have the KitchTrue logo that I added on the card. BROOK stands for basic rules of offering kitchens.

Logo Text

Dennis JonesStar ,Partners LLC. , Registered trainer and proctorwith KitchTrue.

```html
<!DOCTYPE html>
<html lang="en">
<head>
<meta charset="utf-8">
<title>Brook Partners LLC – Business Card</title>
<link rel="stylesheet" href="https://fonts.googleapis.com/css2?family=Montserrat:wght@400;500;600&family=Libre+Baskerville:wght@700&display=swap">
<style>
  :root {
    --backdrop: #1b1b1c;
    --card: #242425;
    --card-edge: #2c2c2d;
    --brand-navy: #2b3e9c;
    --brand-sky: #1fa0de;
    --text-light: #f2f2f2;
    --text-soft: #e6e6e6;
  }
  * { box-sizing: border-box; margin: 0; padding: 0; }
  html, body { width: 1200px; height: 900px; overflow: hidden; }
  body {
    background: var(--backdrop);
    font-family: "Montserrat", sans-serif;
    display: flex;
    flex-direction: column;
    align-items: center;
    justify-content: center;
    gap: 40px;
  }
  .card {
    position: relative;
    width: 660px;
    height: 378px;
    background: linear-gradient(135deg, var(--card-edge), var(--card));
    box-shadow: 0 14px 30px rgba(0,0,0,0.55);
    overflow: hidden;
  }
  .card::after {
    content: "";
    position: absolute;
    left: 0; right: 0; bottom: 0;
    height: 6px;
    background: var(--brand-sky);
  }

  /* Brand lockup */
  .brand { position: absolute; }
  .brand__name-row { display: flex; align-items: center; gap: 8px; }
  .brand__name {
    color: var(--brand-navy);
    font-weight: 600;
    white-space: nowrap;
  }
  .brand__dot {
    border-radius: 50%;
    background: var(--brand-sky);
    flex: none;
  }
  .brand__suffix {
    color: var(--brand-sky);
    font-weight: 500;
    white-space: nowrap;
  }
  .brand__tagline {
    color: var(--text-light);
    font-weight: 500;
    white-space: nowrap;
  }

  /* Front */
  .card--front .brand { left: 50%; top: 118px; transform: translateX(-50%); text-align: center; }
  .card--front .brand__name { font-size: 44px; letter-spacing: 0.5px; }
  .card--front .brand__dot { width: 38px; height: 38px; }
  .card--front .brand__suffix { font-size: 25px; margin-top: -2px; padding-left: 60px; }
  .card--front .brand__tagline { font-size: 20px; margin-top: 6px; }

  /* Back */
  .card--back .brand { left: 34px; top: 112px; }
  .card--back .brand__name { font-size: 27px; }
  .card--back .brand__dot { width: 23px; height: 23px; }
  .card--back .brand__suffix { font-size: 16px; padding-left: 80px; margin-top: -1px; }
  .card--back .brand__tagline { font-size: 12.5px; margin-top: 3px; }

  .credential { position: absolute; left: 38px; top: 236px; }
  .credential__badge { display: block; }
  .credential__note {
    font-family: "Libre Baskerville", serif;
    font-weight: 700;
    font-size: 11px;
    line-height: 1.3;
    color: var(--text-light);
    margin-top: 6px;
  }

  .divider {
    position: absolute;
    left: 362px; top: 92px;
    width: 2px; height: 220px;
    background: var(--brand-sky);
  }

  .contact { position: absolute; left: 384px; top: 98px; right: 20px; color: var(--text-light); }
  .contact__name {
    color: var(--brand-sky);
    font-weight: 500;
    font-size: 26px;
    letter-spacing: 1.2px;
    white-space: nowrap;
  }
  .contact__role { font-size: 17px; margin-top: -2px; color: var(--text-soft); }
  .contact__address { font-size: 15.5px; line-height: 1.35; margin-top: 12px; }
  .contact__list { list-style: none; margin-top: 8px; font-size: 15px; line-height: 1.55; }
  .contact__item { display: flex; align-items: center; gap: 9px; white-space: nowrap; }
  .contact__icon { width: 12px; height: 12px; flex: none; }
</style>
</head>
<body>

  <section class="card card--front" aria-label="Card front">
    <div class="brand">
      <div class="brand__name-row">
        <span class="brand__name">Howard PellBrook</span>
        <span class="brand__dot"></span>
      </div>
      <div class="brand__suffix">Partners LLC.</div>
      <div class="brand__tagline">Registered trainer and proctor with KitchTrue.</div>
    </div>
  </section>

  <section class="card card--back" aria-label="Card back">
    <div class="brand">
      <div class="brand__name-row">
        <span class="brand__name">Howard PellBrook</span>
        <span class="brand__dot"></span>
      </div>
      <div class="brand__suffix">Partners LLC.</div>
      <div class="brand__tagline">Registered trainer and proctor with KitchTrue.</div>
    </div>

    <div class="credential">
      <svg class="credential__badge" width="150" height="56" viewBox="0 0 150 56" role="img" aria-label="KitchTrue certification badge, Allied Eatery Federation">
        <rect x="0" y="6" width="150" height="44" rx="22" fill="#1fa0de"/>
      </svg>
      <p class="credential__note">Registered KitchTrue Proctor<br>&amp; Certified KitchTrue Instructor</p>
    </div>

    <div class="divider"></div>

    <div class="contact">
      <h1 class="contact__name">DANIEL REYES</h1>
      <p class="contact__role">Director</p>
      <p class="contact__address">1825 Alder Lane<br>Milton, MA 02186</p>
      <ul class="contact__list">
        <li class="contact__item">
          <svg class="contact__icon" viewBox="0 0 16 16"><path d="M4 1l3 3-2 2c1 2 3 4 5 5l2-2 3 3-2 3C7 15 1 9 1 3z" fill="#1fa0de"/></svg>
          03 5180 2294
        </li>
        <li class="contact__item">
          <svg class="contact__icon" viewBox="0 0 16 16"><rect x="4" y="1" width="8" height="14" rx="1.5" fill="none" stroke="#1fa0de" stroke-width="1.6"/><circle cx="8" cy="12.5" r="0.9" fill="#1fa0de"/></svg>
          0410 572 318
        </li>
        <li class="contact__item">
          <svg class="contact__icon" viewBox="0 0 16 16"><rect x="1" y="3" width="14" height="10" rx="1" fill="none" stroke="#1fa0de" stroke-width="1.6"/><path d="M1.5 3.5L8 9l6.5-5.5" fill="none" stroke="#1fa0de" stroke-width="1.6"/></svg>
          info@howardpellbrook.com
        </li>
        <li class="contact__item">
          <svg class="contact__icon" viewBox="0 0 16 16"><circle cx="8" cy="8" r="6.5" fill="none" stroke="#1fa0de" stroke-width="1.4"/><ellipse cx="8" cy="8" rx="3" ry="6.5" fill="none" stroke="#1fa0de" stroke-width="1.2"/><path d="M1.5 8h13" stroke="#1fa0de" stroke-width="1.2"/></svg>
          www.howardpellbrook.com
        </li>
      </ul>
    </div>
  </section>

</body>
</html>
```